Clean business card with logo provided

I want a card that will stand out among the masses. I need the color and image to show professionalism and yet have a family appeal showing that I only deal with win/win scenarios. The back of the card will be used to take notes about the individual so I can use that in my database entry. I like modern design but need professionalism in it also. It needs to fit my "clean, safe, and affordable housing" motto. I need to be able to write on the file and update the card details for my employees.

Target Market(s)

Investors looking to make investment income through real estate

Industry/Entity Type

Real Estate

Contact Information for Business Card

Brent Kovalich
blank address, city, st, zip code
480-555-3174
brentkovalich@ridgeworthrentals.example
www.ridgeworthrentals.example

Font styles to use
Sans Serif

Requirements
Must have
• I would like the back of the card to have lines for info. example
• Met/Visited: Date:
• Interets:
Nice to have
• I want the cards color to match the logo background color. Font with details to be san serif and black. I want the card rectangular with square corners. Standard business card size. I would like to see cards designed with both images to see which i prefer more.

```html
<!DOCTYPE html>
<html lang="en">
<head>
<meta charset="utf-8">
<title>Ridgeworth Rentals LLC – Business Card</title>
<link rel="stylesheet" href="https://fonts.googleapis.com/css2?family=Cinzel:wght@400&family=Open+Sans:ital,wght@0,400;1,400&display=swap">
<style>
  :root {
    --page-bg: #8e8e90;
    --card-black: #000000;
    --card-light: #e6e6e8;
    --teal: #1ea3b5;
    --text-light: #d2d2d2;
    --rule-light: #8a8a8a;
    --rule-dark: #222222;
    --white: #ffffff;
  }
  * { box-sizing: border-box; margin: 0; padding: 0; }
  html, body {
    width: 1105px; height: 1200px; overflow: hidden;
    background: var(--page-bg);
  }
  .sheet { position: relative; width: 1105px; height: 1200px; }

  .card {
    position: absolute; left: 182px; width: 740px; height: 428px;
    overflow: hidden;
  }
  .card--front { top: 118px; background: var(--card-black); }
  .card--back { top: 636px; background: var(--card-light); }

  .brand { position: absolute; font-family: "Open Sans", sans-serif; color: var(--teal); }
  .brand__name {
    display: flex; align-items: center; gap: 12px;
    font-size: 30px; font-weight: 400; line-height: 1; white-space: nowrap;
  }
  .brand__mark { width: 22px; height: 22px; background: var(--teal); flex: none; }
  .brand__motto {
    font-size: 12px; letter-spacing: 0.4px; margin-top: 12px;
  }
  .card--front .brand { right: 43px; top: 62px; text-align: right; }
  .card--front .brand__name { justify-content: flex-end; }

  .name-marker { position: absolute; left: 0; top: 238px; width: 11px; height: 36px; background: var(--teal); }
  .holder-name {
    position: absolute; left: 41px; top: 240px;
    font-family: "Cinzel", serif; font-weight: 400; font-size: 27px; color: var(--teal);
    letter-spacing: 0.5px;
  }
  .name-rule { position: absolute; left: 41px; top: 284px; width: 656px; height: 1px; background: var(--rule-light); }

  .contact-list {
    position: absolute; left: 41px; top: 300px; list-style: none;
    font-family: "Open Sans", sans-serif; font-size: 20px; color: var(--text-light);
  }
  .contact-list li { display: flex; align-items: center; height: 29px; }
  .contact-list svg { width: 17px; height: 17px; margin-right: 12px; fill: var(--teal); flex: none; }

  .address {
    position: absolute; right: 43px; top: 329px; text-align: right; font-style: normal;
    font-family: "Open Sans", sans-serif; font-size: 20px; line-height: 29px; color: var(--text-light);
  }

  .back-band { position: absolute; left: 0; top: 0; width: 100%; height: 228px; background: var(--card-black); }
  .card--back .brand { left: 55px; top: 58px; }
  .brand__web {
    font-family: "Open Sans", sans-serif; font-style: italic; font-size: 18px;
    letter-spacing: 2.5px; color: var(--white); margin-top: 12px;
  }

  .note-label {
    position: absolute; font-family: "Open Sans", sans-serif; font-size: 19px;
    color: var(--teal); text-transform: uppercase;
  }
  .note-line { position: absolute; height: 1.5px; background: var(--rule-dark); }
</style>
</head>
<body>
<main class="sheet">

  <section class="card card--front" aria-label="Card front">
    <div class="brand">
      <div class="brand__name"><span class="brand__mark"></span>Ridgeworth Rentals LLC</div>
      <div class="brand__motto">Providing clean, safe, and affordable housing</div>
    </div>

    <div class="name-marker"></div>
    <h1 class="holder-name">BRENT KOVALICH</h1>
    <div class="name-rule"></div>

    <ul class="contact-list">
      <li>
        <svg viewBox="0 0 24 24" aria-hidden="true"><path d="M6.6 10.8a15.1 15.1 0 0 0 6.6 6.6l2.2-2.2c.3-.3.7-.4 1-.2 1.1.4 2.3.6 3.6.6.6 0 1 .4 1 1V20c0 .6-.4 1-1 1A17 17 0 0 1 3 4c0-.6.4-1 1-1h3.5c.6 0 1 .4 1 1 0 1.3.2 2.5.6 3.6.1.3 0 .7-.2 1z"/></svg>
        480-555-3174
      </li>
      <li>
        <svg viewBox="0 0 24 24" aria-hidden="true"><path d="M2 5h20v14H2z"/><path d="M2 5l10 8 10-8" fill="none" stroke="#000" stroke-width="1.6"/></svg>
        brentkovalich@ridgeworthrentals.example
      </li>
      <li>
        <svg viewBox="0 0 24 24" aria-hidden="true"><circle cx="12" cy="12" r="10"/></svg>
        www.ridgeworthrentals.example
      </li>
    </ul>

    <address class="address">
      2140 Larkspur Court<br>
      Juneau, Alaska 99801
    </address>
  </section>

  <section class="card card--back" aria-label="Card back">
    <div class="back-band"></div>
    <div class="brand">
      <div class="brand__name"><span class="brand__mark"></span>Ridgeworth Rentals LLC</div>
      <div class="brand__motto">Providing clean, safe, and affordable housing</div>
      <div class="brand__web">www.ridgeworthrentals.example</div>
    </div>

    <span class="note-label" style="left:55px; top:268px;">Met/Visited:</span>
    <div class="note-line" style="left:188px; top:291px; width:256px;"></div>
    <span class="note-label" style="left:451px; top:268px;">Date:</span>
    <div class="note-line" style="left:511px; top:291px; width:174px;"></div>

    <span class="note-label" style="left:55px; top:320px;">Interets:</span>
    <div class="note-line" style="left:160px; top:343px; width:525px;"></div>

    <div class="note-line" style="left:62px; top:395px; width:623px;"></div>
  </section>

</main>
</body>
</html>
```